KVR Inc Web Design

WHAT ARE WE DOING?
We are developing a new website look and feel for a new company called KVR Inc. This new look and feel should include colors, design elements, choice of photography and other imagery, fonts, and other user experience elements.

WHAT DO THEY DO?
KVR, Inc, makes tools for researchers who are studying protein-protein interactions. These molecules are the basic tools of biology, and serve as key targets for drug developers and disease researchers. The world of proteins is enormously complex, and companies like KVR provide researchers with critical tools that help them elucidate this world.

WHO ARE WE TALKING TO?
The target audience for this website are professional scientists working in university research or biopharma drug development. They are highly sophisticated consumers looking for key tools that will advance their research.

WHAT DO WE WANT THEM TO DO?
The site is an information resource for the customer exploring the tools that KVR sells and the scientific issues surrounding protein-protein interactions. They should be able to navigate easily to their content of choice, while the whole site should convey a professionalism that enhanced KVR’s credibility.

WHAT DOES THE KVR BRAND STAND FOR?
KVR stands for illumination. Proteins are challenging to study, and KVR exists to help shed light on their workings.

WHAT ARE THE KEY VALUES OF THE KVR BRAND?
Integrity. Innovation. Insight.

WHAT ARE THE EXECUTIONAL MANDITORIES?
The look and feel is completely up for grabs. Nothing is off the table.

WHAT ARE THE DELIVERABLES?
We need new designs for the following templates:
http://cms.marlowbench.com/
http://cms.marlowbench.com/products-and-services/instruments-3/bench-top-instruments/
http://cms.marlowbench.com/category/lab-study/

```html
<!DOCTYPE html>
<html lang="en">
<head>
<meta charset="utf-8">
<title>Pipettes — KVR Inc</title>
<link href="https://fonts.googleapis.com/css2?family=Figtree:wght@400;600&family=Open+Sans:wght@400&display=swap" rel="stylesheet">
<style>
  :root {
    --accent: #f7a830;
    --text: #555555;
    --heading: #111111;
    --nav: #5a5a5a;
    --rule: #cfcfcf;
    --tab-bg: #e3e3e3;
    --tab-active: #33b3d8;
    --footer: #6f6f6f;
    --search: #8c8a8a;
  }
  * { box-sizing: border-box; margin: 0; padding: 0; }
  html, body { width: 1200px; height: 1081px; overflow: hidden; background: #fff; }
  body { font-family: "Figtree", Arial, sans-serif; color: var(--text); position: relative; }

  .site-header { position: absolute; top: 0; left: 0; width: 1200px; height: 61px;
    border-top: 3px solid var(--accent); border-bottom: 1px solid #e6e6e6; }
  .brand { position: absolute; left: 120px; top: 13px; font-size: 27px; letter-spacing: 6px;
    color: #6a6a6a; font-weight: 400; }
  .main-nav { position: absolute; left: 305px; top: 19px; display: flex; gap: 23px; }
  .main-nav a { font-size: 16px; font-weight: 600; color: var(--nav); text-decoration: none; }
  .main-nav a.current { color: var(--accent); }
  .search { position: absolute; left: 942px; top: 16px; width: 138px; height: 25px;
    background: var(--search); border-radius: 2px; color: #e8e8e8; font-size: 13px;
    padding: 5px 8px; }
  .search svg { position: absolute; right: 6px; top: 6px; }

  .page-title { position: absolute; left: 119px; top: 93px; font-size: 27px; font-weight: 400; color: var(--heading); }
  .overview-select { position: absolute; left: 886px; top: 97px; width: 194px; height: 25px;
    background: var(--search); color: #f3f3f3; font-size: 13px; padding: 5px 15px; }
  .overview-select svg { position: absolute; right: 10px; top: 10px; }
  .title-rule { position: absolute; left: 120px; top: 130px; width: 960px; height: 4px;
    border-top: 1px solid var(--rule); border-bottom: 1px solid var(--rule); }

  .lead { position: absolute; left: 119px; top: 155px; width: 962px; font-size: 22px;
    line-height: 27px; color: var(--heading); font-weight: 400; }

  .photo { position: absolute; }
  .photo-lab { left: 118px; top: 229px; width: 264px; height: 205px;
    background: linear-gradient(135deg, #d9dde2, #b8c3cf 55%, #8ea6c4); }
  .photo-tube { left: 408px; top: 725px; width: 254px; height: 254px;
    background: linear-gradient(160deg, #3d72b8, #5d8fcf 45%, #c9b8a5 80%, #e6d6c3); }

  .copy { position: absolute; font-size: 13.2px; line-height: 18.75px; }
  .copy p + p { margin-top: 18.75px; }
  .copy a { color: var(--accent); font-weight: 600; text-decoration: none; }
  .copy-main { left: 407px; top: 226px; width: 674px; }
  .copy-tab { left: 675px; top: 722px; width: 405px; }

  .tabs { position: absolute; left: 406px; top: 668px; display: flex; height: 36px; }
  .tabs span { font-family: "Open Sans", Arial, sans-serif; font-size: 16px; color: #555;
    background: var(--tab-bg); display: flex; align-items: center; justify-content: center;
    border-right: 1px solid #fff; position: relative; }
  .tabs span.active { background: var(--tab-active); color: #fff; }
  .tabs span.active::after { content: ""; position: absolute; bottom: -7px; left: 50%;
    margin-left: -7px; border: 7px solid transparent; border-bottom: 0; border-top-color: var(--tab-active); }

  .site-footer { position: absolute; left: 0; top: 1018px; width: 1200px; height: 63px; background: var(--footer); }
  .footer-nav { position: absolute; left: 120px; top: 24px; font-size: 13.5px; color: #fff; }
  .footer-nav a { color: #fff; text-decoration: none; }
  .footer-nav i { font-style: normal; margin: 0 6px; }
  .social { position: absolute; left: 824px; top: 21px; display: flex; gap: 6px; }
  .social span { width: 24px; height: 24px; border-radius: 50%; background: #fff; }
  .copyright { position: absolute; left: 929px; top: 23px; font-size: 15px; color: #fff; }
  .copyright b { color: var(--accent); font-weight: 400; }
</style>
</head>
<body>
<header class="site-header">
  <div class="brand">KVR INC</div>
  <nav class="main-nav">
    <a href="#">Company</a>
    <a href="#" class="current">Products &amp; Services</a>
    <a href="#">Learning Center</a>
    <a href="#">Events</a>
    <a href="#">KVR News</a>
    <a href="#">Contact</a>
  </nav>
  <div class="search">Search
    <svg width="13" height="13" viewBox="0 0 13 13"><circle cx="5" cy="5" r="4" fill="none" stroke="#d8d8d8" stroke-width="1.6"/><line x1="8" y1="8" x2="12" y2="12" stroke="#d8d8d8" stroke-width="2"/></svg>
  </div>
</header>

<h1 class="page-title">PIPETTES</h1>
<div class="overview-select">Product Overview
  <svg width="12" height="7" viewBox="0 0 12 7"><path d="M0 0h12L6 7z" fill="#e5e5e5"/></svg>
</div>
<div class="title-rule"></div>

<h2 class="lead">Donec non massa lacinia, commodo eros eget, rutrum arcu. Integer tincidunt, velit id eleifend nec congue, odio massa consequat mauris, massa consequat</h2>

<div class="photo photo-lab" role="img" aria-label="Two researchers in lab coats and goggles working with a plant sample"></div>

<div class="copy copy-main">
  <p>Donec auctor mollis ligula eget molestie. Aliquam erat volutpat. Curabitur sapien libero, condimentum ac nisl nec, ultricies tincidunt ipsum. Donec in iaculis metus. Mauris eleifend nisi non sapien commodo, hendrerit ornare lacus consectetur. Pellentesque faucibus, purus non dictum lacinia, ante augue pretium neque, vitae egestas dui nisl et enim. Suspendisse iaculis nibh vel lacinia rhoncus Donec auctor mollis ligula eget molestie. Aliquam erat volutpat. Curabitur sapien libero, condimentum ac nisl nec, ultricies tincidunt ipsum. Donec in iaculis metus. Mauris eleifend nisi non sapien commodo, hendrerit ornare lacus consectetur. Pellentesque faucibus, purus non dictum lacinia, ante augue pretium neque, vitae egestas dui nisl et enim.</p>
  <p>Donec auctor mollis ligula eget molestie. Aliquam erat volutpat. Curabitur sapien libero, condimentum ac nisl nec, ultricies tincidunt ipsum. Donec in iaculis metus. Mauris eleifend nisi non sapien commodo, hendrerit ornare lacus consectetur. Pellentesque faucibus, purus non dictum lacinia, ante augue pretium neque, vitae egestas dui nisl et enim. Suspendisse iaculis nibh vel lacinia rhoncus Donec auctor mollis ligula eget molestie. Aliquam erat volutpat. Curabitur sapien libero, condimentum ac nisl nec, ultricies tincidunt ipsum. Donec in iaculis metus. Mauris eleifend nisi non sapien commodo, hendrerit ornare lacus consectetur. Pellentesque faucibus, purus non dictum lacinia, ante augue pretium neque, vitae egestas dui nisl et enim.&nbsp; Donec auctor mollis ligula eget molestie. Aliquam erat volutpat. Curabitur sapien libero, <a href="#">condimentum</a> ac nisl nec, ultricies tincidunt ipsum. Donec in iaculis metus. Mauris eleifend nisi non sapien commodo, hendrerit ornare lacus consectetur. Pellentesque faucibus, purus non dictum lacinia, ante augue pretium neque, vitae egestas dui nisl et enim. Suspendisse iaculis nibh vel lacinia rhoncus Donec auctor mollis ligula eget molestie. Aliquam erat volutpat. Curabitur sapien libero, condimentum ac nisl nec, ultricies tincidunt ipsum. Donec in iaculis metus. Mauris eleifend nisi non sapien commodo, hendrerit ornare lacus consectetur. Pellentesque faucibus, purus non dictum lacinia, ante augue pretium neque, vitae egestas dui nisl et enim.</p>
</div>

<div class="tabs">
  <span class="active" style="width:141px">Overview</span>
  <span style="width:127px">Features</span>
  <span style="width:167px">Specifications</span>
  <span style="width:111px">FAQ's</span>
  <span style="width:129px;border-right:0">Manuals</span>
</div>

<div class="photo photo-tube" role="img" aria-label="Gloved researcher pipetting a pink liquid into a test tube"></div>

<div class="copy copy-tab">
  <p>Quisque feugiat lacus vitae posuere blandit. Nulla sit amet laoreet felis, id rhoncus nisl. Aenean fringilla quam in nibh egestas, in malesuada tortor accumsan. Donec non massa lacinia, commodo eros eget, rutrum arcu. Integer tincidunt, velit id eleifend congue, odio massa consequat mauris, a scelerisque nulla nulla eu nulla. Cras luctus pulvinar nibh ut viverra. Aenean vestibulum vitae justo non dictum. Mauris ut tellus in dui pretium dictum nec non tortor. Nulla a velit quis dolor interdum <a href="#">scelerisque</a> eu et nisl.</p>
  <p>Donec auctor mollis ligula eget molestie. Aliquam erat volutpat. Curabitur sapien libero, condimentum ac nisl nec, ultricies tincidunt ipsum. Donec in iaculis metus. Mauris eleifend nisi non sapien commodo, hendrerit ornare lacus consectetur. Pellentesque faucibus, purus non dictum lacinia, ante augue</p>
</div>

<footer class="site-footer">
  <nav class="footer-nav">
    <a href="#">Company</a><i>-</i><a href="#">Products &amp; Services</a><i>-</i><a href="#">Learning Center</a><i>-</i><a href="#">Events</a><i>-</i><a href="#">KVR News</a><i>-</i><a href="#">Contact</a>
  </nav>
  <div class="social"><span></span><span></span><span></span></div>
  <div class="copyright">Copyright © <b>KVR Inc.</b> 2013</div>
</footer>
</body>
</html>
```